Varnex Consulting Business card design.

See our website www.varnexconsulting.example which will give you a good idea of what we are about. The font is called 'Play'.

I'd like a standout business card in keeping with the themes and branding on the website

Target Market(s)

professionals. HR directors

Industry/Entity Type

Business

Contact Information for Business Card

Varnex Consulting PO Box 3172 Merrowdale NSW 2291 1300 485 193 Gavin Threlkeld Principal email: career@varnexconsulting.example ABN: 71203948865

Font styles to use
Other font styles liked:
• Play

Requirements
Must have
• Must have same design colours and branding as website.
• On back I'd prefer a list of the things we do which appears below the name at the header on the website

```html
<!DOCTYPE html>
<html lang="en">
<head>
<meta charset="utf-8">
<title>Varnex Consulting – Business Card</title>
<link href="https://fonts.googleapis.com/css2?family=Open+Sans:ital,wght@0,400;0,600;1,400&family=Play:wght@400;700&display=swap" rel="stylesheet">
<style>
  :root {
    --navy: #0d1f33;
    --blue: #3a8fd1;
    --white: #ffffff;
    --page: #ececea;
    --ink: #12243a;
  }
  html, body {
    margin: 0;
    padding: 0;
    width: 1189px;
    height: 1200px;
    overflow: hidden;
    background: var(--page);
  }
  .canvas {
    position: relative;
    width: 1189px;
    height: 1200px;
  }
  .card {
    position: absolute;
    left: 167px;
    width: 855px;
    height: 488px;
    background: var(--white);
    box-shadow: 0 6px 14px rgba(0,0,0,0.18);
  }
  .card--front { top: 68px; }
  .card--back  { top: 626px; }
  .card svg { display: block; width: 855px; height: 488px; }

  .brand { font-family: 'Play', sans-serif; font-weight: 700; font-size: 57px; letter-spacing: 1px; }
  .brand--light { fill: var(--white); }
  .brand--blue  { fill: var(--blue); }
  .brand--navy  { fill: var(--navy); }

  .person-name { font-family: 'Play', sans-serif; font-weight: 700; font-size: 33px; fill: var(--white); letter-spacing: 0.5px; }
  .person-role { font-family: 'Play', sans-serif; font-size: 22px; fill: var(--blue); }
  .phone { font-family: 'Open Sans', sans-serif; font-size: 22px; fill: var(--white); }

  .contact { font-family: 'Open Sans', sans-serif; font-size: 22px; fill: var(--white); }

  .section-label { font-family: 'Play', sans-serif; font-weight: 700; font-size: 25px; fill: var(--blue); }
  .services { font-family: 'Play', sans-serif; font-size: 22px; fill: var(--ink); }
  .testimonial { font-family: 'Open Sans', sans-serif; font-style: italic; font-size: 19.5px; fill: var(--ink); }
  .address { font-family: 'Play', sans-serif; font-weight: 700; font-size: 22px; fill: var(--white); letter-spacing: 0.5px; }
</style>
</head>
<body>
<main class="canvas">

  <!-- Front of card -->
  <section class="card card--front" aria-label="Business card front">
    <svg viewBox="0 0 855 488" xmlns="http://www.w3.org/2000/svg">
      <defs>
        <linearGradient id="track-tone" x1="0" y1="0" x2="0" y2="1">
          <stop offset="0" stop-color="#3b3f4a"/>
          <stop offset="0.45" stop-color="#b88a78"/>
          <stop offset="1" stop-color="#7a3a30"/>
        </linearGradient>
        <linearGradient id="snow-tone" x1="0" y1="0" x2="0" y2="1">
          <stop offset="0" stop-color="#1f5fa6"/>
          <stop offset="0.5" stop-color="#3f86c9"/>
          <stop offset="0.7" stop-color="#e8eef5"/>
          <stop offset="1" stop-color="#ffffff"/>
        </linearGradient>
        <linearGradient id="surf-tone" x1="0" y1="0" x2="0" y2="1">
          <stop offset="0" stop-color="#9a9c9e"/>
          <stop offset="0.5" stop-color="#d6d8d9"/>
          <stop offset="1" stop-color="#3c6a6a"/>
        </linearGradient>
      </defs>

      <rect class="header-band" x="0" y="0" width="855" height="183" fill="var(--navy)"/>
      <text class="brand brand--light" x="39" y="86">VARNEX</text>
      <text class="brand brand--blue" x="39" y="153">CONSULTING</text>

      <text class="person-name" x="818" y="73" text-anchor="end">Employee Name</text>
      <text class="person-role" x="818" y="94" text-anchor="end">Managing Director</text>
      <text class="phone" x="782" y="151" text-anchor="end">1300 485 193</text>
      <g class="icon-phone" transform="translate(792,128)">
        <rect width="26" height="26" fill="var(--blue)"/>
        <path d="M9 6 q-3 1 -2 6 q2 6 8 9 q3 1 5 -2 l-3 -3 l-2 1 q-3 -2 -4 -5 l1 -2 z" fill="var(--white)"/>
      </g>

      <g class="photo-strip" transform="translate(0,197)">
        <polygon role="img" aria-label="Photo: sprinters' hands on the start line of a running track" points="0,0 300,0 269,203 0,203" fill="url(#track-tone)"/>
        <polygon role="img" aria-label="Photo: snowboarder jumping over a snowy peak against blue sky" points="307,0 588,0 551,203 276,203" fill="url(#snow-tone)"/>
        <polygon role="img" aria-label="Photo: surfer riding a breaking wave" points="595,0 855,0 855,203 558,203" fill="url(#surf-tone)"/>
      </g>

      <rect class="contact-band" x="0" y="415" width="855" height="73" fill="var(--blue)"/>
      <g class="icon-mail" transform="translate(38,440)">
        <rect width="26" height="24" fill="var(--white)"/>
        <rect x="3" y="5" width="20" height="14" fill="none" stroke="var(--blue)" stroke-width="1.5"/>
        <path d="M3 5 L13 13 L23 5 M3 19 L10 12 M23 19 L16 12" fill="none" stroke="var(--blue)" stroke-width="1.5"/>
      </g>
      <text class="contact" x="72" y="461">career@varnexconsulting.example</text>
      <g class="icon-web" transform="translate(458,440)">
        <rect width="26" height="24" fill="var(--white)"/>
        <circle cx="13" cy="12" r="8.5" fill="none" stroke="var(--blue)" stroke-width="1.5"/>
        <ellipse cx="13" cy="12" rx="3.5" ry="8.5" fill="none" stroke="var(--blue)" stroke-width="1.2"/>
        <path d="M4.5 12 H21.5 M6 7.5 H20 M6 16.5 H20" stroke="var(--blue)" stroke-width="1.2"/>
      </g>
      <text class="contact" x="818" y="461" text-anchor="end">www.varnexconsulting.example</text>
    </svg>
  </section>

  <!-- Back of card -->
  <section class="card card--back" aria-label="Business card back">
    <svg viewBox="0 0 855 488" xmlns="http://www.w3.org/2000/svg">
      <text class="brand" x="427.5" y="125" text-anchor="middle"><tspan class="brand--navy">VARNEX</tspan> <tspan class="brand--blue">CONSULTING</tspan></text>

      <text class="section-label" x="427.5" y="198" text-anchor="middle">WE DO</text>
      <text class="services" x="427.5" y="237" text-anchor="middle">Search &amp; Selection | Career Coaching | Talent Assessment</text>
      <text class="services" x="427.5" y="272" text-anchor="middle">Resume Enhancement | Interview Coaching | Leadership Development</text>
      <text class="services" x="427.5" y="306" text-anchor="middle">Personal Development Plans | Outplacement</text>

      <text class="testimonial" x="427.5" y="365" text-anchor="middle">“I really loved working with Varnex.</text>
      <text class="testimonial" x="427.5" y="399" text-anchor="middle">They really understood my needs and my plans for my professional future.”</text>

      <rect class="rule" x="0" y="422" width="855" height="6" fill="var(--navy)"/>
      <rect class="address-band" x="0" y="428" width="855" height="60" fill="var(--blue)"/>
      <text class="address" x="427.5" y="466" text-anchor="middle">PO Box 3172 Merrowdale NSW 2291</text>
    </svg>
  </section>

</main>
</body>
</html>
```